Letterhead and matching envelope design for a dental office

We need a new stationary design, letterhead and envelope #10, for a dental office in Denver area. We are called Bright Harbor Dental. We want a simple and minimalistic design but not a boring design. I wish to have one good point that makes it look professional. I have attached our logo. Feel free to use either one. I want the design for letterhead and envelope look like a "matching pair" but not look the same. The envelope doesn't have to be white and it will have an address window on bottom left.

Target Market(s)

everyone who visits dentist (adults)

Industry/Entity Type

Dental

Font styles to use
Other font styles liked:
• close to font on logo or something that matches well

Requirements
Must have
• professional
• simple, minimalistic
• unique point that stands out
Nice to have
• matching but not same design for letterhead and envelope
Should not have
• not look like all the other boring designs
• no flowery, distracting feats

```html
<!DOCTYPE html>
<html lang="en">
<head>
<meta charset="utf-8">
<title>Bright Harbor Dental — Stationery</title>
<link href="https://fonts.googleapis.com/css2?family=Cinzel:wght@600&family=Open+Sans:wght@400;600&display=swap" rel="stylesheet">
<style>
  :root{
    --bg:#0f9a58;
    --brand:#1aa84a;
    --paper:#ffffff;
    --mist:#eef1ef;
    --swoosh:#dfe3e1;
    --ink:#5b5f5d;
    --ink-dark:#2f3331;
  }
  *{box-sizing:border-box;margin:0;padding:0}
  html,body{width:1200px;height:900px;overflow:hidden;background:var(--bg)}
  .canvas{position:relative;width:1200px;height:900px;font-family:"Open Sans",Arial,sans-serif}

  .wordmark{font-family:"Cinzel",Georgia,serif;font-weight:600;color:var(--brand);letter-spacing:.12em;white-space:nowrap;display:flex;align-items:center;gap:8px}
  .wordmark .dot{width:8px;height:8px;border-radius:50%;background:var(--brand)}

  /* Envelope #10 */
  .envelope{position:absolute;left:50px;top:150px;width:560px;height:242px;background:linear-gradient(160deg,var(--mist) 0%,var(--paper) 45%);overflow:hidden;box-shadow:0 10px 24px rgba(0,0,0,.18)}
  .envelope .swooshes{position:absolute;inset:0;width:100%;height:100%}
  .envelope .wordmark{position:absolute;left:30px;top:24px;font-size:15px}
  .envelope .return-address{position:absolute;left:30px;top:48px;font-size:8px;color:var(--ink)}
  .envelope .window{position:absolute;left:30px;top:118px;width:226px;height:82px;border:1px solid #d4d8d6;border-radius:8px}
  .envelope .contacts{position:absolute;left:30px;bottom:14px;right:30px;display:flex;justify-content:space-between;font-size:7.5px;color:var(--ink)}

  /* Letterhead */
  .letterhead{position:absolute;left:650px;top:70px;width:500px;height:707px;background:var(--paper);overflow:hidden;box-shadow:0 12px 28px rgba(0,0,0,.2)}
  .letterhead .swooshes{position:absolute;left:0;width:100%}
  .letterhead .swooshes.top{top:0;height:150px}
  .letterhead .swooshes.bottom{bottom:0;height:220px}
  .letterhead .wordmark{position:absolute;right:46px;top:68px;font-size:19px}
  .letterhead .footer{position:absolute;left:28px;right:28px;bottom:22px;color:var(--ink);font-size:8px;line-height:1.7}
  .letterhead .footer .name{font-family:"Cinzel",Georgia,serif;font-weight:600;color:var(--brand);letter-spacing:.12em;font-size:11px}
  .letterhead .footer .row{display:flex;gap:14px;flex-wrap:wrap}
  .letterhead .footer .ids{color:var(--ink-dark);font-weight:600}
  .icon{display:inline-block;width:8px;height:8px;border-radius:50%;background:var(--brand);vertical-align:-1px;margin-right:3px}
</style>
</head>
<body>
<main class="canvas">

  <section class="envelope" aria-label="Envelope front">
    <svg class="swooshes" viewBox="0 0 560 242" preserveAspectRatio="none" aria-hidden="true">
      <path d="M160 60 C300 120 430 150 560 120 L560 132 C430 165 300 135 160 60Z" fill="var(--swoosh)" opacity=".7"/>
      <path d="M300 242 C380 200 470 190 560 200 L560 242Z" fill="var(--mist)"/>
    </svg>
    <div class="wordmark"><span class="dot"></span>Bright Harbor Dental</div>
    <p class="return-address">1480 Larkspur Ave, Suite 210, Denver, CO 80204</p>
    <div class="window" aria-label="Address window"></div>
    <div class="contacts">
      <span><i class="icon"></i>303.555.0148</span>
      <span><i class="icon"></i>303.555.0192</span>
      <span><i class="icon"></i>hello@brightharbordental.com</span>
      <span><i class="icon"></i>www.brightharbordental.com</span>
    </div>
  </section>

  <section class="letterhead" aria-label="Letterhead">
    <svg class="swooshes top" viewBox="0 0 500 150" preserveAspectRatio="none" aria-hidden="true">
      <path d="M0 20 C150 70 330 100 500 80 L500 0 L0 0Z" fill="var(--mist)"/>
      <path d="M60 60 C220 110 380 125 500 108 L500 118 C380 138 220 122 60 60Z" fill="var(--swoosh)"/>
    </svg>
    <div class="wordmark"><span class="dot"></span>Bright Harbor Dental</div>
    <svg class="swooshes bottom" viewBox="0 0 500 220" preserveAspectRatio="none" aria-hidden="true">
      <path d="M0 40 C120 90 260 120 420 118 L420 126 C260 132 110 110 0 60Z" fill="var(--swoosh)"/>
      <path d="M0 90 C150 130 330 150 500 140 L500 220 L0 220Z" fill="var(--mist)"/>
    </svg>
    <div class="footer">
      <div class="name">Bright Harbor Dental</div>
      <div class="row">
        <span><i class="icon"></i>1480 Larkspur Ave, Suite 210, Denver, CO 80204</span>
        <span><i class="icon"></i>303.555.0148</span>
        <span><i class="icon"></i>303.555.0192</span>
      </div>
      <div class="row">
        <span class="ids">Provider No. 000000W &nbsp;|&nbsp; ABN 00 000 000 000</span>
        <span><i class="icon"></i>hello@brightharbordental.com</span>
        <span><i class="icon"></i>www.brightharbordental.com</span>
      </div>
    </div>
  </section>

</main>
</body>
</html>
```